Can you make a cool and versatile Tarn Meridian Powerpoint template?
See www.tarnmeridian-example.co.uk and http://www.examplenet.invalid/company/tarn-meridian-ltd/ (on the right) to see how the logos are currently used - with interchangeably white and black backgrounds.
Target Market(s)
Marketing managers, product managers in HR technology, HR consultants
Industry/Entity Type
It Company
Font styles to use
Sans Serif
Requirements
Must have
- Master slide design, fonts, color theme, etc. Ideally two variations - one with white background (using colorful logo), one with a darker background (using black/white logo).

```html
<!DOCTYPE html>
<html lang="en">
<head>
<meta charset="utf-8">
<title>Tarn Meridian – Master Slide</title>
<link rel="stylesheet" href="https://fonts.googleapis.com/css2?family=Graduate&family=Open+Sans:wght@400;600&display=swap">
<style>
  :root {
    --page: #ffffff;
    --slide-light: #e9e9e9;
    --slide-mid: #dcdcdc;
    --frame: #3a3a3c;
    --band: #333335;
    --accent: #27a9e1;
    --white: #ffffff;
    --photo-dark: #6b2a06;
    --photo-mid: #e07a10;
    --photo-light: #ffd27a;
  }
  * { box-sizing: border-box; margin: 0; padding: 0; }
  html, body { width: 1200px; height: 900px; overflow: hidden; background: var(--page); }
  .canvas { position: relative; width: 1200px; height: 900px; font-family: "Open Sans", Arial, sans-serif; }

  .slide {
    position: absolute; left: 17px; top: 168px; width: 1160px; height: 652px;
    background:
      radial-gradient(ellipse at 70% 30%, rgba(255,255,255,.7), transparent 60%),
      linear-gradient(180deg, var(--slide-light), var(--slide-mid));
  }

  .photo-frame {
    position: absolute; left: 30px; top: 34px; width: 638px; height: 428px;
    background: var(--frame); padding: 9px 11px;
  }
  .photo {
    width: 100%; height: 100%;
    background:
      radial-gradient(ellipse at 65% 15%, var(--photo-light) 0%, transparent 45%),
      linear-gradient(160deg, var(--photo-mid) 0%, #c85e08 50%, var(--photo-dark) 100%);
  }

  .slide-number {
    position: absolute; right: 15px; top: 13px; width: 103px; height: 103px;
  }
  .slide-number span {
    position: absolute; right: 14px; top: 18px;
    font-family: "Graduate", "Arial Black", sans-serif; font-size: 22px; color: var(--white);
  }

  .title-band {
    position: absolute; left: 17px; top: 495px; width: 1127px; height: 145px;
    background: var(--band);
  }
  .slide-title {
    position: absolute; left: 23px; top: 14px;
    font-family: "Graduate", "Arial Black", sans-serif; font-size: 66px; line-height: 1;
    color: var(--accent); letter-spacing: 1px;
  }
  .title-rule {
    position: absolute; left: 24px; top: 91px; width: 422px; height: 3px; background: var(--white);
  }
  .slide-details {
    position: absolute; left: 80px; top: 104px;
    font-size: 19px; color: var(--white); letter-spacing: .2px;
  }
  .contact {
    position: absolute; right: 175px; top: 60px; text-align: right;
    font-size: 11px; line-height: 17px; color: var(--white);
  }
  .brand {
    position: absolute; right: 11px; top: 11px; width: 148px; height: 123px;
    background: var(--accent);
    display: flex; align-items: center; justify-content: center;
    font-size: 19px; font-weight: 600; color: var(--white); text-align: center; line-height: 1.2;
  }
</style>
</head>
<body>
<div class="canvas">
  <section class="slide">
    <div class="photo-frame">
      <div class="photo" role="img" aria-label="Warm golden-hour photograph of a person holding a dandelion in a sunlit field"></div>
    </div>

    <div class="slide-number">
      <svg width="103" height="103" viewBox="0 0 103 103" aria-hidden="true">
        <polygon points="0,0 103,0 103,103" fill="var(--accent)"/>
      </svg>
      <span>02</span>
    </div>

    <div class="title-band">
      <h1 class="slide-title">SLIDE TITLE</h1>
      <div class="title-rule"></div>
      <p class="slide-details">DETAILS OF SLIDE / NAME OF PRESENTOR</p>
      <p class="contact">WWW.TARNMERIDIAN-EXAMPLE.CO.UK<br>HELLO@TARNMERIDIAN-EXAMPLE.CO.UK</p>
      <div class="brand">Tarn<br>Meridian</div>
    </div>
  </section>
</div>
</body>
</html>
```